New Company Business Card design

Looking for a corporate looking business card utilising my new logo design - the logo i would like embossed as one option and flat as another - simplistic but stylish - less is more - we are an import export business launching into the market - i would like a couple of options as main background - Grey or Black

```html
<!DOCTYPE html>
<html lang="en">
<head>
<meta charset="utf-8">
<title>Meridian Trade Partners – Business Card</title>
<link rel="stylesheet" href="https://fonts.googleapis.com/css2?family=Cinzel:wght@400;600&display=swap">
<style>
  :root {
    --page-bg: #d8d5d1;
    --card-bg: #252525;
    --brand-blue: #1f7fd0;
    --text-light: #f2f2f2;
    --text-grey: #8c8c8c;
    --rule: #bdbdbd;
  }
  * { margin: 0; padding: 0; box-sizing: border-box; }
  html, body {
    width: 1200px;
    height: 419px;
    overflow: hidden;
    background: var(--page-bg);
  }
  .canvas {
    width: 1200px;
    height: 419px;
    display: flex;
    justify-content: center;
    align-items: center;
    gap: 60px;
    font-family: "Cinzel", serif;
  }
  .card {
    width: 500px;
    height: 286px;
    background: var(--card-bg);
    border-radius: 3px;
    box-shadow: 0 8px 22px rgba(0, 0, 0, 0.28);
    display: flex;
    flex-direction: column;
    justify-content: center;
    align-items: center;
    text-align: center;
  }

  /* Front */
  .brand {
    display: flex;
    flex-direction: column;
    align-items: center;
  }
  .brand-mark {
    width: 64px;
    height: 64px;
    border-radius: 50%;
    background: var(--brand-blue);
    margin-bottom: 14px;
  }
  .brand-name {
    color: var(--brand-blue);
    font-size: 21px;
    font-weight: 600;
    letter-spacing: 0.5px;
    text-transform: uppercase;
  }
  .brand-rule {
    width: 250px;
    height: 1px;
    background: var(--text-grey);
    margin: 6px 0 5px;
  }
  .brand-tagline {
    color: var(--text-grey);
    font-size: 10px;
    letter-spacing: 1.5px;
    text-transform: uppercase;
  }

  /* Back */
  .contact { color: var(--text-light); }
  .contact-name {
    color: var(--brand-blue);
    font-size: 20px;
    letter-spacing: 1px;
    text-transform: uppercase;
    line-height: 1.1;
  }
  .contact-title {
    font-size: 14px;
    letter-spacing: 0.5px;
    text-transform: uppercase;
  }
  .contact-rule {
    width: 70px;
    height: 1px;
    background: var(--rule);
    margin: 9px auto;
  }
  .contact-line {
    font-size: 12.5px;
    line-height: 1.4;
  }
  .contact-line.caps { text-transform: uppercase; font-size: 11.5px; }
</style>
</head>
<body>
<main class="canvas">
  <section class="card card-front" aria-label="Card front">
    <div class="brand">
      <div class="brand-mark"></div>
      <p class="brand-name">Meridian Trade Partners</p>
      <div class="brand-rule"></div>
      <p class="brand-tagline">Trusted trade across every border</p>
    </div>
  </section>

  <section class="card card-back" aria-label="Card back">
    <div class="contact">
      <p class="contact-name">Daniel Hart</p>
      <p class="contact-title">CEO/Founder</p>
      <div class="contact-rule"></div>
      <p class="contact-line">4120 Willow Crest Road</p>
      <p class="contact-line">Juneau, Alaska 99801</p>
      <div class="contact-rule"></div>
      <p class="contact-line">P. 555 204 7719</p>
      <p class="contact-line caps">hello@meridiantrade.com</p>
      <p class="contact-line caps">www.meridiantrade.com</p>
    </div>
  </section>
</main>
</body>
</html>
```